Project Overview:
We are looking to create a website for a monthly subscription IPTV service in WordPress. The website should provide a seamless user experience for customers to sign up for the service and manage their account information. We need the following pages: Home Page, Product Page, Sign-Up Page, and Account Information Page.

Home Page:
The Home Page design should be simple and clean, with a dark theme and minimalistic design elements. We would like to include graphics of popular movie shows displayed on multiple devices. The page should highlight the key benefits and features of our service and provide a clear call-to-action for visitors to sign up.

Product Page:
The Product Page should provide detailed information about our subscription tiers and pricing plans. It should highlight the key features of each plan and provide a clear comparison between them. The page should also include a call-to-action button for visitors to sign up.

Sign-Up Page:
The Sign-Up Page is the conversion page where members will sign up for the service. It should collect the following information: Name, Phone Number, Email, Password, and Payment Information. The design should be simple, intuitive, and easy to use. It should highlight the benefits of our service and provide a clear call-to-action for visitors to sign up.

Account Information Page:
The Account Information Page should allow members to view and manage their account details. It should include the following information: Profile Image, Contact Details, Password Management, Payment Information Management, and Membership Expiration Date. The design should be user-friendly, intuitive, and easy to navigate.

Goals: The primary goal of the website is to provide an easy-to-use portal for customers to sign up for the service and manage their account information. The website should be user-friendly and visually appealing to attract potential customers.

Scope: The scope of the project includes designing a home page, a sign-up page, an account information page, and a payment information page. The website should be designed to be responsive and accessible on desktop and mobile devices.

Design Preferences: The design should be clean, modern, and visually appealing. The use of a color palette that is consistent with the brand identity is recommended. The website should be easy to navigate and provide a clear call-to-action for users to sign up for the service.

FYI: The subscription service I am designing a website for is related to an IPTV service. IPTV stands for Internet Protocol Television, which is a digital television broadcasting protocol that uses the internet to deliver TV programs and videos to viewers. The website will allow customers to sign up for the IPTV service and access their account information such as user name and password, membership tier, name, and payment details. Please let me know if you have any further questions, and I would be happy to provide more details. Thank you!

Dear Designers,

Thank you for your participation in our project. After reviewing the designs received so far, we have decided to update the brief to better reflect our needs and preferences. We apologize for any confusion this may cause, but we believe that these changes will result in better design submissions and a more successful project overall.

The updated brief is as follows:

We are looking to create a website for WordPress.

Also, here is the updated Brief.

Project Title: WordPress Website Design for Monthly Subscription IPTV Service

Project Overview:
We are looking to create a website for a monthly subscription IPTV service. The website should provide a seamless user experience for customers to sign up for the service and manage their account information. We need the following pages: Home Page, Product Page, Sign-Up Page, and Account Information Page.

Home Page:

Product Page:

Sign-Up Page:

Account Information Page:

Design Preferences:
We prefer a dark theme with minimalistic design elements and hits of our logo colors. The website should be easy to use and navigate, with clear calls-to-action and simple, intuitive forms. The design should be optimized for mobile devices and load quickly.

We hope that these updates provide you with a clearer understanding of our requirements and preferences. Please let us know if you have any questions or concerns. We look forward to seeing your revised designs.

Thank you again for your participation.
We will guarantee this project as soon as we see something we like that meets the updated requirements.

The website's target audience is individuals who are interested in subscribing to the monthly service.

4 page

• One item for sale and a client profile section.

```html
<!DOCTYPE html>
<html lang="en">
<head>
<meta charset="utf-8">
<title>VIZORA – IPTV Subscription</title>
<link href="https://fonts.googleapis.com/css2?family=Roboto:ital,wght@0,400;0,500;0,700;0,900;1,400&family=Rubik:ital,wght@1,800;1,900&display=swap" rel="stylesheet">
<style>
:root{
  --red:#f20000;
  --pink:#f9e2e2;
  --ink:#1c1c1c;
  --text:#555;
  --white:#fff;
  --black:#0b0b0b;
  --line:#dcdcdc;
}
*{margin:0;padding:0;box-sizing:border-box}
html,body{width:1200px;height:4494px;overflow:hidden}
body{position:relative;font-family:'Roboto',sans-serif;color:var(--ink);background:var(--white)}
.abs{position:absolute}
.brand{font-family:'Roboto',sans-serif;font-weight:900;letter-spacing:1px}
.title{font-family:'Rubik',sans-serif;font-style:italic;font-weight:900;color:var(--red);text-transform:uppercase;-webkit-text-stroke:1.5px #400;letter-spacing:-0.5px}
.btn{position:absolute;display:flex;align-items:center;justify-content:center;gap:10px;background:var(--red);color:var(--white);font-weight:700;font-size:15px;text-transform:uppercase;border-radius:4px}
.btn svg{width:14px;height:14px}

.site-header{left:0;top:0;width:1200px;height:80px;background:var(--white)}
.site-header .brand{left:112px;top:18px;font-size:38px;color:var(--red)}
.main-nav{left:398px;top:30px;display:flex;gap:22px;font-size:15px;font-weight:500}
.main-nav span.sep{color:#888}
.main-nav .active{color:var(--red)}
.signup{left:956px;top:17px;width:134px;height:46px;border:2px solid #900}

.hero{left:0;top:80px;width:1200px;height:612px;background:linear-gradient(100deg,#1b2830 0%,#2f4652 40%,#406274 70%,#2c3f48 100%)}
.hero-welcome{left:108px;top:242px;font-family:'Rubik',sans-serif;font-style:italic;font-weight:900;color:var(--white);font-size:26px}
.hero-name{left:108px;top:284px;font-family:'Roboto',sans-serif;font-weight:900;color:var(--white);font-size:104px;line-height:1}
.hero-copy{left:109px;top:402px;width:460px;color:var(--white);font-size:15.5px;line-height:26px}
.hero-cta{left:109px;top:479px;width:160px;height:46px}

.about-frame{left:84px;top:968px;width:360px;height:282px;background:var(--red);border-radius:0 0 30px 30px}
.about-photo{left:102px;top:778px;width:478px;height:454px;border-radius:20px;background:linear-gradient(135deg,#c9b8a4,#8d7a66 45%,#3d4f63 100%)}
.about-title{left:637px;top:800px;font-size:33px}
.about-copy{left:637px;top:862px;width:470px;font-size:15px;line-height:25.7px;color:var(--text);text-align:justify}
.about-cta{left:637px;top:1173px;width:160px;height:47px;border:2px solid #900}

.why{left:0;top:1318px;width:1200px;height:614px;background:var(--pink)}
.why-title{left:0;width:1200px;top:1398px;text-align:center;font-size:33px}
.feature{position:absolute;top:1518px;width:313px;height:324px;border-radius:70px 0 70px 0;text-align:center;padding:30px 22px 0}
.feature.red{background:var(--red);color:var(--white)}
.feature.light{background:var(--white);color:var(--ink)}
.feature .icon{width:94px;height:94px;margin:0 auto 16px;border-radius:50%;display:flex;align-items:center;justify-content:center}
.feature.red .icon{background:var(--white)}
.feature.light .icon{background:var(--red)}
.feature h3{font-size:18px;font-weight:700;margin-bottom:12px}
.feature p{font-size:14px;line-height:22px}
.feature.light p{color:var(--text)}
.feature .more{margin-top:16px;font-size:15px;font-weight:700;display:flex;justify-content:center;gap:8px;align-items:center}
.feature.light .more{color:var(--red)}

.services-title{left:0;width:1200px;top:2012px;text-align:center;font-size:33px}
.service{position:absolute;width:310px;background:var(--white);border-radius:14px;box-shadow:0 6px 18px rgba(0,0,0,.18);padding:8px;text-align:center}
.service .thumb{height:230px;border-radius:8px}
.service h3{font-size:15px;font-weight:500;margin:34px 0 16px;text-transform:uppercase}
.service p{font-size:14px;line-height:24px;color:var(--text);padding:0 14px}
.service .btn{position:relative;margin:20px auto 26px;width:134px;height:40px}

.video-title{left:0;width:1200px;top:2682px;text-align:center;font-size:33px}
.band{left:0;top:2884px;width:1200px;height:580px;background:linear-gradient(160deg,#ff1a1a,#e30000 60%,#f00)}
.video{left:228px;top:2764px;width:746px;height:372px;border:4px solid var(--white);background:linear-gradient(90deg,#1a1a1a,#3b3530 45%,#5a4c48 70%,#30202a)}
.play{left:582px;top:2933px;width:38px;height:38px;border-radius:50%;background:rgba(255,255,255,.85);display:flex;align-items:center;justify-content:center}

.reviews-title{left:365px;top:3186px;font-family:'Rubik',sans-serif;font-style:italic;font-weight:900;color:var(--white);font-size:33px;text-transform:uppercase}
.avatar{left:226px;top:3255px;width:100px;height:100px;transform:rotate(45deg);border-radius:10px;background:linear-gradient(135deg,#aac4de,#5b82aa)}
.quote-mark{left:326px;top:3228px;font-family:'Rubik',sans-serif;font-size:60px;line-height:1;color:rgba(255,255,255,.35)}
.quote{left:365px;top:3254px;width:650px;color:var(--white);font-style:italic;font-size:15px;line-height:26px}
.author{left:365px;top:3356px;color:var(--white);font-size:18px;font-weight:500}
.role{left:365px;top:3384px;color:var(--white);font-size:12px}
.arrow{top:3284px;width:40px;height:40px}

.contact-title{left:0;width:1200px;top:3542px;text-align:center;font-size:33px}
.field{position:absolute;height:42px;border:1px solid var(--line);border-radius:4px;box-shadow:0 2px 6px rgba(0,0,0,.06);display:flex;align-items:center;gap:12px;padding-left:22px;font-size:13px;color:#333}
.field svg{width:12px;height:12px}
.field.area{align-items:flex-start;padding-top:20px}
.submit{left:520px;top:3923px;width:159px;height:49px;border:2px solid #900}

.site-footer{left:0;top:4060px;width:1200px;height:434px;background:var(--black)}
.footer-brand{left:112px;top:4160px;font-size:46px;color:var(--red)}
.socials{left:150px;top:4240px;display:flex;gap:14px}
.socials span{width:12px;height:12px;border-radius:50%;background:var(--white)}
.foot-h{font-size:17px;font-weight:700;color:var(--white)}
.contact-item{left:383px;display:flex;gap:10px;font-size:12.5px;line-height:17px;color:var(--white)}
.contact-item b{display:block;font-size:11px}
.contact-item svg{width:12px;height:12px;margin-top:2px;flex:none}
.company-links{left:685px;top:4196px;font-size:13px;line-height:34px;color:var(--white)}
.help{left:850px;top:4196px;width:230px;font-size:12px;line-height:19px;color:var(--white)}
.touch{left:850px;top:4275px;width:193px;height:44px;border-radius:3px;font-size:14px}
.rule{left:112px;top:4412px;width:980px;border-top:1px dashed #666}
.go-up{left:1012px;top:4401px;width:80px;height:20px;border-radius:10px;background:#444;color:var(--white);font-size:11px;font-weight:700;display:flex;align-items:center;justify-content:center}
.copyright{left:112px;top:4445px;font-size:13px;color:var(--white)}
.legal{left:765px;top:4445px;font-size:13px;display:flex;gap:8px;color:var(--white)}
</style>
</head>
<body>

<header class="site-header abs">
  <div class="brand abs">VIZORA</div>
  <nav class="main-nav abs">
    <span class="active">HOME</span><span class="sep">|</span>
    <span>ABOUT US</span><span class="sep">|</span>
    <span>SERVICES</span><span class="sep">|</span>
    <span>BLOG</span><span class="sep">|</span>
    <span>CONTACT US</span>
  </nav>
  <div class="btn signup">SIGN UP <svg viewBox="0 0 16 16"><circle cx="8" cy="5" r="3.5" fill="#fff"/><path d="M1 16c0-4 3-6 7-6s7 2 7 6z" fill="#fff"/></svg></div>
</header>

<section class="hero abs" role="img" aria-label="Friends on a sofa watching television with popcorn"></section>
<div class="hero-welcome abs">WELCOME TO</div>
<div class="hero-name abs">VIZORA</div>
<p class="hero-copy abs">Lorem ipsum dolor sit amet consectetur adipiscing elit sed do eiusmod tempor incididunt ut labore et dolore magna aliqua.</p>
<div class="btn hero-cta">GET STARTED <svg viewBox="0 0 16 16"><circle cx="8" cy="8" r="8" fill="#fff"/><path d="M6 4l4 4-4 4" stroke="#f20000" stroke-width="2" fill="none"/></svg></div>

<div class="about-frame abs"></div>
<div class="about-photo abs" role="img" aria-label="Couple in a living room choosing channels on a wall-mounted smart TV"></div>
<h2 class="title about-title abs">About VIZORA</h2>
<p class="about-copy abs">Lorem ipsum dolor sit amet consectetur adipiscing elited sed do eiusmod tempor incididunt ut labore et dolore magna aliqua. Ut enim ad minim veniam, quis nostrud exercitation ullamco laboris nisi ut aliquip ex ea commodo consequat. Duis aute irure dolor in reprehenderit in voluptate velit esse cillum dolore eu fugiat nulla pariatur. Excepteur sint occaecat cupidatat non proident, sunt in culpa qui officia deserunt mollit anim id est laborumLorem ipsum dolor sit amet, consectetur adipiscing elit, sed do eiusmod tempor incididunt ut labore et dolore magna aliqua. Ut enim ad minim veniam, nostrud exercitation ullamco laboris nisi aliquipcommodo consequat. Duis aute irure reprehenderit in voluptate velit esseg.</p>
<div class="btn about-cta">GET STARTED <svg viewBox="0 0 16 16"><circle cx="8" cy="8" r="8" fill="#fff"/><path d="M6 4l4 4-4 4" stroke="#f20000" stroke-width="2" fill="none"/></svg></div>

<section class="why abs"></section>
<h2 class="title why-title abs">Why Choose Us</h2>
<div class="feature red" style="left:112px">
  <div class="icon"><svg width="52" height="52" viewBox="0 0 52 52" fill="none" stroke="#f20000" stroke-width="2.5"><rect x="6" y="10" width="40" height="26" rx="2"/><path d="M18 44h16M26 36v8"/></svg></div>
  <h3>Lorem ipsum dolor sit amet</h3>
  <p>Lorem ipsum dolor sit amet consectetur adipiscing eiusmoded tempor incididunt labore et dolore magna aliqua enim ad minim veniam nostrud exercitation.</p>
  <div class="more">READ MORE <svg width="14" height="14" viewBox="0 0 16 16"><circle cx="8" cy="8" r="8" fill="#fff"/><path d="M6 4l4 4-4 4" stroke="#f20000" stroke-width="2" fill="none"/></svg></div>
</div>
<div class="feature light" style="left:444px">
  <div class="icon"><svg width="52" height="52" viewBox="0 0 52 52" fill="none" stroke="#fff" stroke-width="2.5"><rect x="6" y="10" width="30" height="22" rx="2"/><rect x="32" y="18" width="12" height="26" rx="3"/><path d="M14 40h14"/></svg></div>
  <h3>Lorem ipsum dolor sit amet,</h3>
  <p>Lorem ipsum dolor sit amet consectetur adipiscing eiusmoded tempor incididunt labore et dolore magna aliqua enim ad minim veniam nostrud exercitation.</p>
  <div class="more">READ MORE <svg width="14" height="14" viewBox="0 0 16 16"><circle cx="8" cy="8" r="8" fill="#f20000"/><path d="M6 4l4 4-4 4" stroke="#fff" stroke-width="2" fill="none"/></svg></div>
</div>
<div class="feature red" style="left:775px">
  <div class="icon"><svg width="52" height="52" viewBox="0 0 52 52" fill="none" stroke="#f20000" stroke-width="2.5"><rect x="8" y="8" width="36" height="28" rx="2"/><path d="M14 44h24"/><circle cx="26" cy="22" r="6"/></svg></div>
  <h3>Lorem ipsum dolor sit amet,</h3>
  <p>Lorem ipsum dolor sit amet consectetur adipiscing eiusmoded tempor incididunt labore et dolore magna aliqua enim ad minim veniam nostrud exercitation.</p>
  <div class="more">READ MORE <svg width="14" height="14" viewBox="0 0 16 16"><circle cx="8" cy="8" r="8" fill="#fff"/><path d="M6 4l4 4-4 4" stroke="#f20000" stroke-width="2" fill="none"/></svg></div>
</div>

<h2 class="title services-title abs">Our Services</h2>
<article class="service" style="left:108px;top:2100px">
  <div class="thumb" role="img" aria-label="Family watching an outdoor television on a patio" style="background:linear-gradient(135deg,#7a8c7e,#3e4d48 60%,#22302c)"></div>
  <h3>Lorem ipsum dolor sit amet</h3>
  <p>Lorem ipsum dolor sit ametconsectetur adipiscing elited sed do eiusmod tempor incididunt ut labore eted dolore magna.</p>
  <div class="btn">READ MORE</div>
</article>
<article class="service" style="left:446px;top:2124px">
  <div class="thumb" role="img" aria-label="Family watching sport on a large TV in a dark room" style="background:linear-gradient(135deg,#3a4656,#141a22 60%,#0c0f14)"></div>
  <h3>Lorem ipsum dolor sit amet</h3>
  <p>Lorem ipsum dolor sit ametconsectetur adipiscing elited sed do eiusmod tempor incididunt ut labore eted dolore magna.</p>
  <div class="btn">READ MORE</div>
</article>
<article class="service" style="left:782px;top:2100px">
  <div class="thumb" role="img" aria-label="Viewer with popcorn browsing a streaming menu" style="background:linear-gradient(135deg,#4a3a36,#7a5e52 50%,#2a201e)"></div>
  <h3>Lorem ipsum dolor sit amet</h3>
  <p>Lorem ipsum dolor sit ametconsectetur adipiscing elited sed do eiusmod tempor incididunt ut labore eted dolore magna.</p>
  <div class="btn">READ MORE</div>
</article>

<h2 class="title video-title abs">Our Video</h2>
<div class="band abs"></div>
<div class="video abs" role="img" aria-label="Video still of a viewer on a sofa facing a TV full of show tiles"></div>
<div class="play abs"><svg width="14" height="14" viewBox="0 0 14 14"><path d="M3 1l10 6-10 6z" fill="#333"/></svg></div>

<h2 class="reviews-title abs">What Our Clients Have To Say</h2>
<div class="avatar abs" role="img" aria-label="Client portrait"></div>
<div class="quote-mark abs">“</div>
<p class="quote abs">Lorem ipsum dolor sit amet, consectetur adipiscing elit, sed do eiusmod tempor incididunt ut labore et dolore magna aliqua. Ut enim ad minim veniam, quis nostrud exercitation ullamco laboris nisi ut aliquip ex ea commodo consequat. Duis aute irure dolor in reprehenderit in</p>
<div class="author abs">Dara Whitlow</div>
<div class="role abs">Sed ut perspiciatis</div>
<svg class="arrow abs" style="left:145px" viewBox="0 0 40 40"><path d="M26 6L12 20l14 14" stroke="#fff" stroke-width="4" fill="none"/></svg>
<svg class="arrow abs" style="left:1100px" viewBox="0 0 40 40"><path d="M14 6l14 14-14 14" stroke="#fff" stroke-width="4" fill="none"/></svg>

<h2 class="title contact-title abs">Contact Us</h2>
<div class="field" style="left:160px;top:3620px;width:432px"><svg viewBox="0 0 16 16"><circle cx="8" cy="5" r="3.5" fill="#333"/><path d="M1 16c0-4 3-6 7-6s7 2 7 6z" fill="#333"/></svg>User Name</div>
<div class="field" style="left:606px;top:3620px;width:434px"><svg viewBox="0 0 16 16"><ellipse cx="8" cy="8" rx="7" ry="4.5" fill="none" stroke="#333" stroke-width="1.6"/><circle cx="8" cy="8" r="2" fill="#333"/></svg>Password</div>
<div class="field" style="left:160px;top:3682px;width:432px"><svg viewBox="0 0 16 16"><circle cx="5" cy="5" r="3" fill="#333"/><circle cx="11" cy="5" r="3" fill="#333"/><path d="M0 15c0-4 2-6 5-6s5 2 5 6zM8 15c0-3 1-6 3-6s5 2 5 6z" fill="#333"/></svg>Membership Tier</div>
<div class="field" style="left:606px;top:3682px;width:434px"><svg viewBox="0 0 16 16"><circle cx="8" cy="5" r="3.5" fill="#333"/><path d="M1 16c0-4 3-6 7-6s7 2 7 6z" fill="#333"/></svg>Name</div>
<div class="field area" style="left:160px;top:3742px;width:880px;height:148px"><svg viewBox="0 0 16 16"><ellipse cx="6" cy="6" rx="6" ry="4.5" fill="#333"/><ellipse cx="11" cy="10" rx="5" ry="4" fill="#333"/></svg>Payment Details</div>
<div class="btn submit">SUBMIT NOW <svg viewBox="0 0 16 16"><path d="M1 8l14-7-4 14-3-6z" fill="#fff"/></svg></div>

<footer class="site-footer abs"></footer>
<div class="brand footer-brand abs">VIZORA</div>
<div class="socials abs"><span></span><span></span><span></span><span></span></div>

<div class="foot-h abs" style="left:383px;top:4152px">Contact Us</div>
<div class="contact-item abs" style="top:4195px"><svg viewBox="0 0 16 16"><path d="M3 1l3 3-2 2c1 3 3 5 6 6l2-2 3 3-2 2C6 15 1 10 1 3z" fill="#f20000"/></svg><div><b>Phone</b>+1 555 014 2290</div></div>
<div class="contact-item abs" style="top:4246px"><svg viewBox="0 0 16 16"><rect x="1" y="3" width="14" height="10" fill="#f20000"/><path d="M1 3l7 6 7-6" stroke="#fff" fill="none"/></svg><div><b>Email</b>info@vizora.tv</div></div>
<div class="contact-item abs" style="top:4297px"><svg viewBox="0 0 16 16"><path d="M8 1a5 5 0 015 5c0 4-5 9-5 9S3 10 3 6a5 5 0 015-5z" fill="#f20000"/><circle cx="8" cy="6" r="2" fill="#000"/></svg><div><b>Location</b>939 Lorem ipsum dolor sit amet<br>consectetur elited</div></div>

<div class="foot-h abs" style="left:685px;top:4152px">Company</div>
<div class="company-links abs">Home<br>About Us<br>Services<br>Blog<br>Contact us</div>

<div class="foot-h abs" style="left:850px;top:4152px">Stil have questios?</div>
<p class="help abs">Contact us using this form. A representative will aswer your questions as soon as possible.</p>
<div class="btn touch">GET IN TOUCH</div>

<div class="rule abs"></div>
<div class="go-up abs">↑ Go Up</div>
<div class="copyright abs">© 2023 VIZORA | All Rights Reserved</div>
<div class="legal abs"><span>Privacy Policy</span>|<span>Cookie Policy</span>|<span>Terms Of Services</span></div>

</body>
</html>
```